Torvane Email Signature Banners – Fabrication Capability Series

www.Torvane.com.au is an Australian engineering and fabrication company specialising in fabrication and welding of :
steel piping spools,
skids and frames,
small volume process steel tanks
and general steel fabrication
We require four distinct banner designs for use in Microsoft Lintaro email signatures. Each banner will highlight a specific capability while maintaining a consistent brand identity.
Deliverables
Four banners total:
Piping Spools Fabrication – focus on precision welding and stainless steel pipework
Skid & Frames Fabrication – highlight skid systems and structural frames
Small Steel Tanks Fabrication – show fabricated tanks and workshop craftsmanship
General Fabrication Solutions – broad steel fabrication theme for company-wide use
Dimensions: 600–700 px wide × 100 px high
Format: PNG (preferred), small file size prefered
Resolution: 72 dpi
Background: non-transparent, industrial or workshop setting
Text examples:
1. Piping Spools Fabrication
Option A: “Expert Fabrication Solutions for Process Piping”
Option B: “Precision Welding for Complex Systems”
Option C: “Delivering Quality in Every Spool”
Option D: “Engineered for Flow, Built for Strength”
2. Skid & Frames Fabrication
Option A: “Custom Engineered Modular Systems”
Option B: “Built Strong. Designed Smart.”
Option C: “Reliable Frames for Industrial Performance”
Option D: “Modular Fabrication for Seamless Integration”
3. Small Steel Tanks Fabrication
Option A: “Precision Built for Your Needs”
Option B: “Compact Strength. Proven Durability.”
Option C: “Fabricated for Performance and Longevity”
Option D: “Small Tanks. Big Reliability.”
4. General Fabrication Solutions
Option A: “Quality Craftsmanship, Proven Results”
Option B: “Your Partner in Precision Fabrication”
Option C: “Engineering Excellence in Every Weld”
Option D: “Australian Fabrication. Global Standards.”
Style Direction
Clean, professional, and engineering‑focused
Use Torvane brand colours
Blend photo realism with vector clarity (no heavy gradients)
Include subtle industrial textures or workshop imagery
Typography: bold sans‑serif, legible at small scale
Usage Context
These banners will appear at the bottom of staff email signatures via Lintaro Email Signature Tool for Microsoft 365, so clarity and fast loading are essential. No Logo is required in the banners.
Reference
Existing Torvane signature is attached. Colour palette to match the signature style and logo.
Target Market(s)
Engineering and construction companies,
Industry/Entity Type
Engineering fabrication design
Look and feel

```html
<!DOCTYPE html>
<html lang="en">
<head>
<meta charset="utf-8">
<title>Torvane – Skid &amp; Frames Fabrication Banner</title>
<link href="https://fonts.googleapis.com/css2?family=Montserrat:wght@600;800&display=swap" rel="stylesheet">
<style>
  :root {
    --brand-blue: #1d4c9f;
    --brand-blue-light: #2457ad;
    --accent-cyan: #2aa6e0;
    --photo-sky: #b9c6cf;
    --photo-metal: #8e9499;
    --photo-ground: #a58d6c;
    --text-white: #ffffff;
  }
  html, body {
    margin: 0;
    padding: 0;
    width: 1200px;
    height: 200px;
    overflow: hidden;
    background: var(--brand-blue);
  }
  .banner {
    position: relative;
    width: 1200px;
    height: 200px;
    overflow: hidden;
    background: var(--brand-blue);
    font-family: "Montserrat", Arial, sans-serif;
    color: var(--text-white);
  }
  .banner__shapes {
    position: absolute;
    inset: 0;
    width: 1200px;
    height: 200px;
  }
  .banner__headline {
    position: absolute;
    left: 44px;
    top: 42px;
    margin: 0;
    font-weight: 800;
    font-size: 36px;
    line-height: 56px;
    letter-spacing: 0.3px;
    text-transform: uppercase;
  }
  .banner__capability {
    position: absolute;
    left: 812px;
    top: 104px;
    margin: 0;
    font-weight: 600;
    font-size: 25px;
    letter-spacing: 0.2px;
  }
</style>
</head>
<body>
  <div class="banner">
    <svg class="banner__shapes" viewBox="0 0 1200 200" aria-hidden="false">
      <defs>
        <linearGradient id="photoTones" x1="0" y1="0" x2="0" y2="1">
          <stop offset="0" stop-color="var(--photo-sky)"/>
          <stop offset="0.45" stop-color="var(--photo-metal)"/>
          <stop offset="1" stop-color="var(--photo-ground)"/>
        </linearGradient>
      </defs>
      <polygon class="banner__panel-right" points="800,0 1200,0 1200,200 690,200" fill="var(--brand-blue-light)"/>
      <polygon class="banner__accent-stripe" points="566,0 590,0 474,200 450,200" fill="var(--accent-cyan)"/>
      <polygon class="banner__photo" points="588,0 800,0 690,200 472,200" fill="url(#photoTones)"
               role="img" aria-label="Photo of a fabricated steel pipe skid with valves on a site"/>
    </svg>
    <h1 class="banner__headline">Custom Engineered<br>Modular Systems</h1>
    <p class="banner__capability">Skid &amp; Frames Fabrication</p>
  </div>
</body>
</html>
```